Past Every River Oz Tour Flyer

I need a dynamic flyer for a concert tour.
I have uploaded the file. Please use these ingredients for the design.
The font for the title is Jellyka Jellyfish lower case from www.glyphbarn.example
Updates
We are getting close!! We just need bright colours, the headings to STAND OUT and Byron Bay has to be moved to under NSW Bellingen.
Thanks for all your hard work!
Target Market(s)
We are targeting a wide range of customers from old age to children and families
Industry/Entity Type
Tour
Look and feel
Each slider illustrates characteristics of the customer's brand and the style your logo design should communicate.

```html
<!DOCTYPE html>
<html lang="en">
<head>
<meta charset="utf-8">
<title>Past Every River – Australia Tour Flyer</title>
<link rel="stylesheet" href="https://fonts.googleapis.com/css2?family=Sacramento&family=Bebas+Neue&family=Lato:wght@700&family=Roboto+Condensed:wght@700&display=swap">
<style>
  :root{
    --gold:#d8c13c;
    --gold-deep:#b9a02a;
    --gold-light:#ebe08a;
    --red:#c80d12;
    --red-deep:#9c0a0d;
    --leather:#2b2a27;
    --leather-dark:#1c1b19;
    --ink:#111;
    --white:#fff;
    --yellow:#ffe600;
  }
  *{margin:0;padding:0;box-sizing:border-box}
  html,body{width:900px;height:1200px;overflow:hidden;background:#e9e9e9}
  .flyer{position:relative;width:900px;height:1200px;overflow:hidden;
    background:radial-gradient(ellipse at 50% 40%,var(--gold-light) 0%,var(--gold) 45%,var(--gold-deep) 100%)}
  .title-band{position:absolute;left:0;top:52px;width:900px;height:150px;
    background:linear-gradient(180deg,var(--red) 0%,var(--red-deep) 100%);
    display:flex;align-items:center;justify-content:center}
  .tour-title{font-family:"Sacramento",cursive;color:var(--white);font-size:118px;line-height:1;
    margin-top:6px;letter-spacing:1px}
  .choir-name{position:absolute;left:0;width:900px;top:228px;text-align:center;
    font-family:"Bebas Neue",sans-serif;font-size:74px;color:var(--ink);letter-spacing:1px;line-height:1}
  .tour-sub{position:absolute;left:0;width:900px;top:298px;text-align:center;
    font-family:"Lato",sans-serif;font-weight:700;font-size:40px;color:var(--red)}
  .venue-panel{position:absolute;left:0;top:412px;width:900px;height:486px;
    background:radial-gradient(ellipse at 70% 40%,#3a3935 0%,var(--leather) 50%,var(--leather-dark) 100%)}
  .contact-band{position:absolute;left:0;top:903px;width:900px;height:166px;
    background:linear-gradient(180deg,var(--red) 0%,var(--red-deep) 100%)}
  .photo-frame{position:absolute;left:40px;top:369px;width:460px;height:795px;
    background:#f1e9a4;padding:11px;box-shadow:0 4px 14px rgba(0,0,0,.45)}
  .photo{width:100%;height:100%;
    background:radial-gradient(ellipse at 45% 35%,#d98a2c 0%,#a5581c 35%,#5e3414 70%,#2a1a0c 100%)}
  .region{position:absolute;left:500px;width:400px;text-align:center}
  .region-head{display:block;margin:0 auto;width:300px;height:30px;line-height:30px;
    background:linear-gradient(90deg,rgba(200,13,18,0) 0%,var(--red) 25%,var(--red) 75%,rgba(200,13,18,0) 100%);
    font-family:"Roboto Condensed",sans-serif;font-size:22px;color:var(--yellow);letter-spacing:.5px}
  .towns{position:absolute;left:540px;width:340px;display:grid;grid-template-columns:209px 1fr;
    row-gap:3px;font-family:"Roboto Condensed",sans-serif;font-size:19px;color:var(--white);line-height:20px}
  .towns.single{grid-template-columns:1fr;text-align:center;left:500px;width:400px}
  .contact{position:absolute;left:540px;font-family:"Roboto Condensed",sans-serif;line-height:1}
  .contact-label{color:var(--yellow);font-size:27px}
  .contact-value{color:var(--white);font-size:38px}
  .partners{position:absolute;top:1100px;left:596px;display:flex;gap:26px;align-items:center}
  .partner{display:flex;align-items:center;gap:8px;font-family:"Roboto Condensed",sans-serif;
    font-size:22px;color:var(--ink)}
  .partner-mark{width:18px;height:18px;background:var(--red)}
</style>
</head>
<body>
<div class="flyer">
  <div class="title-band"><h1 class="tour-title">Past Every River</h1></div>
  <h2 class="choir-name">The Harmony Children's Choir</h2>
  <p class="tour-sub">Australia Tour</p>

  <div class="venue-panel"></div>
  <div class="contact-band"></div>

  <div class="photo-frame">
    <div class="photo" role="img" aria-label="Young choir dancer in orange costume and straw skirt performing on stage"></div>
  </div>

  <div class="region" style="top:428px"><span class="region-head">VICTORIA</span></div>
  <div class="towns" style="top:471px">
    <span>Geelong</span><span>Bendigo</span>
    <span>Sunbury</span><span>Albury</span>
    <span>Melbourne</span><span></span>
  </div>

  <div class="region" style="top:553px"><span class="region-head">A.C.T.</span></div>
  <div class="towns single" style="top:598px"><span>Canberra</span></div>

  <div class="region" style="top:636px"><span class="region-head">N.S.W.</span></div>
  <div class="towns" style="top:679px">
    <span>Nowra</span><span>Port Macquarie</span>
    <span>Sydney</span><span>Laurieton</span>
    <span>Wollongong</span><span>Taree</span>
    <span>Blue Mountains</span><span>Bellingen</span>
  </div>

  <div class="region" style="top:787px"><span class="region-head">QLD</span></div>
  <div class="towns" style="top:838px">
    <span>Byron Bay</span><span>Sunshine</span>
    <span>Gold Coast</span><span>Coast</span>
  </div>

  <div class="contact" style="top:921px"><span class="contact-label">LENA MARLOW</span></div>
  <div class="contact" style="top:952px"><span class="contact-value">0400 812 356</span></div>
  <div class="contact" style="top:997px"><span class="contact-label">TICKETS &amp; INFO</span></div>
  <div class="contact" style="top:1027px"><span class="contact-value" style="font-size:34px">www.choirtour.example</span></div>

  <div class="partners">
    <div class="partner"><span class="partner-mark"></span>Songbird</div>
    <div class="partner">Harmony Hills</div>
  </div>
</div>
</body>
</html>
```